Re designing of website of VELTRIS Pens, an International stationary brand

We would like to re design our existing website veltrispens.com. We are leading manufacturers and exporters of stationary products. Our existence is global -selling and marketing in all 5 continents.

We are a 35year old group with focus on high quality, innovative designs and state of art manufacturing setup.

Client satisfaction by committed service and trust are the roots of our organisation.

We would like to see a website which focuses on our brand Veltris and must have an international appeal. Our target buyers would be Agents, distributors and wholesalers in various countries. Content would be similar to our existing website but designing and outlook needs to be totally different.

For the outlook we do like the following websites from our industry which can be used to draw inspiration.
1. www.duniverastationery.com
2. www.quorlapen.com
3. www.haltmivopen.com

The homepage need not be focused on the product but must emphasis on the branding of Veltris, our existence of 35years along with international presence and quality standards maintained by our organisation.
Updates

Reason: Would like to see some more concepts and designs as per artwork attached.

Target Market(s)

Wholesalers, Agents and Distributors in all countries around the world. Target market is global

Number of Pages Required

1 page

Font styles to use
Sans Serif

Requirements
Must have
• Focus on Branding, High Quality Standards, Customer Loyalty
Nice to have
• Like the outlook of the websites
• www.haltmivopen.com
• www.duniverastationery.com
• www.quorlapen.com
Should not have
• Don't like the outlook of our present website www.veltrispens.com
• It doesn't justify our brand or our product

```html
<!DOCTYPE html>
<html lang="en">
<head>
<meta charset="utf-8">
<title>Veltris Pens – World Class Writing Instruments</title>
<link rel="stylesheet" href="https://fonts.googleapis.com/css2?family=Source+Sans+3:ital,wght@0,300;0,400;0,600;0,700;1,400&family=Oswald:wght@300;400&display=swap">
<style>
:root{
  --brand-red:#ec1c24;
  --white:#ffffff;
  --ink:#222222;
  --page-grey:#efefef;
  --muted:#9a9a9a;
  --line:#e2e2e2;
  --amber:#f5b50a;
  --footer:#000000;
}
*{box-sizing:border-box;margin:0;padding:0}
html,body{width:1200px;height:1047px;overflow:hidden}
body{position:relative;background:var(--page-grey);font-family:"Source Sans 3",Arial,sans-serif;color:var(--ink)}

/* header */
.site-header{position:absolute;left:0;top:0;width:1200px;height:102px;background:var(--brand-red);color:var(--white)}
.brand{position:absolute;left:86px;top:24px;display:flex;align-items:center;gap:10px}
.brand-square{width:52px;height:52px;background:var(--white)}
.brand-name{font-size:46px;font-weight:400;letter-spacing:1px;line-height:1;color:var(--white)}
.call-us{position:absolute;right:262px;top:23px;font-size:16px;font-weight:600;white-space:nowrap}
.call-us strong{font-weight:700;margin-right:10px}
.lang-select{position:absolute;left:959px;top:18px;width:155px;height:30px;border:1px solid var(--white);font-size:14px;padding:5px 10px;display:flex;justify-content:space-between;align-items:center;white-space:nowrap}
.lang-select svg{width:8px;height:5px}
.main-nav{position:absolute;top:64px;right:86px;display:flex;gap:27px;font-size:14.5px;text-transform:uppercase}
.main-nav .active{font-weight:700;position:relative}
.main-nav .active::after{content:"";position:absolute;left:0;right:0;top:34px;height:3px;background:var(--white)}
.caret{display:inline-block;width:0;height:0;border-left:3.5px solid transparent;border-right:3.5px solid transparent;border-top:4px solid var(--white);margin-left:6px;vertical-align:middle}

/* hero */
.hero{position:absolute;left:0;top:102px;width:1200px;height:498px;background:linear-gradient(180deg,#f7f7f7 0%,#ededed 60%,#f6f6f6 100%);overflow:hidden}
.hero-rings{position:absolute;left:0;top:0}
.hero-product{position:absolute;left:560px;top:14px;width:80px;height:420px;background:linear-gradient(180deg,rgba(90,92,160,.18) 0%,rgba(60,62,140,.22) 55%,rgba(40,40,40,.2) 80%,rgba(200,200,200,.12) 100%)}
.hero-title{position:absolute;left:0;width:1200px;top:136px;text-align:center;font-size:84px;font-weight:300;color:var(--brand-red);letter-spacing:1px;line-height:1}
.hero-copy{position:absolute;left:290px;width:620px;top:233px;text-align:center;font-size:16.5px;letter-spacing:1.2px;line-height:22px;color:var(--ink)}
.hero-copy strong{font-weight:700}
.slider-dots{position:absolute;top:449px;left:560px;display:flex;gap:9px}
.slider-dots span{width:14px;height:14px;border:1.5px solid #555;border-radius:50%}
.slider-dots .current{border-color:var(--brand-red)}

/* feature panels */
.exports-panel{position:absolute;left:86px;top:650px;width:540px;height:279px;overflow:hidden;color:var(--white)}
.exports-visual{position:absolute;inset:0;background:radial-gradient(ellipse at 60% 90%,#6b5a2a 0%,#243554 40%,#0f1d36 75%,#0b1426 100%)}
.exports-content{position:absolute;left:30px;top:30px;width:480px}
.exports-content h2{font-size:30px;font-weight:400;letter-spacing:1px;line-height:1}
.exports-content p{margin-top:18px;width:470px;font-size:13px;line-height:23px;color:#e4e8ef}
.read-more{display:block;margin-top:20px;font-size:15.5px;font-weight:700}

.events-panel{position:absolute;left:638px;top:650px;width:476px;height:279px;background:var(--white)}
.events-title{position:absolute;left:14px;top:32px;font-size:32px;font-weight:400;letter-spacing:1px;line-height:1}
.events-arrows{position:absolute;left:390px;top:30px}
.sort-label{position:absolute;right:16px;top:72px;font-size:11.5px;font-style:italic;color:#555;text-transform:uppercase}
.events-month{position:absolute;left:15px;top:84px;font-family:"Oswald",sans-serif;font-weight:300;font-size:22px;color:#c8c8c8}
.sort-row{position:absolute;right:16px;top:96px;display:flex;align-items:center;font-size:9.5px;color:#bbb;text-transform:uppercase;gap:6px}
.sort-row .val{color:#444;font-size:10.5px}
.sort-row .sep{width:1px;height:16px;background:var(--line);margin:0 4px}
.pill{background:#b9b9b9;color:var(--white);font-size:9px;padding:1px 5px;border-radius:3px}
.event-list{position:absolute;left:14px;top:117px;width:444px;border:1px solid var(--line)}
.event{position:relative;height:70px;border-left:3px solid var(--brand-red);border-bottom:1px solid var(--line)}
.event:last-child{border-bottom:0}
.event.amber{border-left-color:var(--amber)}
.event-date{position:absolute;left:14px;top:8px;font-family:"Oswald",sans-serif;color:#aaa}
.event-date .dow{font-size:7px;text-transform:uppercase;display:block}
.event-date .day{font-size:27px;line-height:24px}
.event-date .mon{font-size:8px;display:block;text-transform:uppercase}
.event-date .range{font-size:13px;position:absolute;left:37px;top:9px;white-space:nowrap}
.event-date .range small{font-size:6px}
.event-info{position:absolute;left:80px;top:12px;width:350px}
.event-info h3{font-family:"Oswald",sans-serif;font-weight:400;font-size:17px;color:#555;text-transform:uppercase;line-height:1}
.event-meta{margin-top:6px;font-size:10.5px;color:#999;line-height:13px}
.event-org{font-size:8.5px;font-style:italic;color:#aaa}
.event-org b{font-weight:400;color:#666}

/* footer */
.site-footer{position:absolute;left:0;top:946px;width:1200px;height:101px;background:var(--footer);color:var(--white)}
.footer-brand{position:absolute;left:86px;top:31px;display:flex;align-items:center;gap:7px}
.footer-brand .brand-square{width:34px;height:34px}
.footer-brand .brand-name{font-size:29px}
.copyright{position:absolute;left:272px;top:42px;font-size:13px;text-transform:uppercase}
.legal-links{position:absolute;right:86px;top:41px;font-size:13px;text-transform:uppercase;display:flex;gap:14px}
</style>
</head>
<body>

<header class="site-header">
  <div class="brand"><span class="brand-square"></span><span class="brand-name">VELTRIS</span></div>
  <div class="call-us"><strong>CALL US NOW!</strong>91 22 24310587 – 91 22 24319630</div>
  <div class="lang-select">SELECT LANGUAGE
    <svg viewBox="0 0 8 5"><path d="M0 0h8L4 5z" fill="#fff"/></svg>
  </div>
  <nav class="main-nav">
    <span class="active">Home</span>
    <span>About Us</span>
    <span>Products<i class="caret"></i></span>
    <span>Promotional Products</span>
    <span>Careers</span>
    <span>Enquiry Form</span>
    <span>Contact</span>
  </nav>
</header>

<section class="hero">
  <svg class="hero-rings" width="1200" height="498" viewBox="0 0 1200 498">
    <circle cx="600" cy="228" r="168" fill="none" stroke="#dcdcdc" stroke-width="1"/>
    <circle cx="600" cy="228" r="130" fill="none" stroke="#e2e2e2" stroke-width="1"/>
    <circle cx="600" cy="228" r="96" fill="#e2e2e2"/>
    <circle cx="600" cy="228" r="26" fill="#eec0c0"/>
  </svg>
  <div class="hero-product" role="img" aria-label="Photo of a blue metal ballpoint pen with black grip standing upright"></div>
  <h1 class="hero-title">VELTRIS METAL PENS</h1>
  <p class="hero-copy">We are leading manufacturers and exporters of stationary products. Our existence is global<br><strong>Selling and marketing in all 5 continents</strong></p>
  <div class="slider-dots"><span></span><span></span><span class="current"></span><span></span></div>
</section>

<section class="exports-panel">
  <div class="exports-visual" role="img" aria-label="Night view of the earth with glowing export routes between continents"></div>
  <div class="exports-content">
    <h2>COUNTRIES OF EXPORTS</h2>
    <p>Duis autem vel eum iriure dolor in hendrerit in vulputate velit esse molestie<br>consequat, vel illum dolore eu feugiat nulla facilisis at vero eros et accumsan et iusto<br>odio dignissim qui blandit praesent luptatum zzril delenit augue duis dolore te feugait<br>nulla facilisi.</p>
    <span class="read-more">Read More</span>
  </div>
</section>

<section class="events-panel">
  <h2 class="events-title">EVENTS</h2>
  <svg class="events-arrows" width="70" height="34" viewBox="0 0 70 34">
    <circle cx="17" cy="17" r="15" fill="none" stroke="#d8d8d8"/>
    <path d="M19 11l-6 6 6 6" fill="none" stroke="#c4c4c4" stroke-width="1.5"/>
    <circle cx="53" cy="17" r="15" fill="none" stroke="#d8d8d8"/>
    <path d="M51 11l6 6-6 6" fill="none" stroke="#c4c4c4" stroke-width="1.5"/>
  </svg>
  <div class="sort-label">Sort Options</div>
  <div class="events-month">JUNE, 2014</div>
  <div class="sort-row">
    <span>Sort by:</span><span class="val">Date</span><i class="caret" style="border-top-color:#999"></i>
    <span class="sep"></span>
    <span class="val">Country:</span><span class="pill">ALL</span>
    <span class="val" style="margin-left:10px">City:</span><span class="pill">ALL</span>
  </div>
  <div class="event-list">
    <article class="event amber">
      <div class="event-date"><span class="dow">Fri</span><span class="day">20</span><span class="mon">Jun</span><span class="range">- 15 <small>JUL</small></span></div>
      <div class="event-info">
        <h3>Camping Trip</h3>
        <div class="event-meta">◷ 8:00 am - (July 15) 5:00 am</div>
      </div>
    </article>
    <article class="event">
      <div class="event-date"><span class="dow">Thu</span><span class="day">26</span><span class="mon">Jun</span></div>
      <div class="event-info">
        <h3>Cinco de Mayo</h3>
        <div class="event-meta">◷ 10:00 am - 3:00 pm &nbsp;⌖ 42 Harlow Ave Linden, NY 11290</div>
        <div class="event-org">Event Organized By: <b>Riverside Community Guild</b></div>
      </div>
    </article>
  </div>
</section>

<footer class="site-footer">
  <div class="footer-brand"><span class="brand-square"></span><span class="brand-name">VELTRIS</span></div>
  <div class="copyright">© 2010 - 2015. VELTRIS PENS PVT. LTD. All rights reserved.</div>
  <nav class="legal-links"><span>Terms &amp; Conditions</span><span>|</span><span>Privacy</span></nav>
</footer>

</body>
</html>
```